Estate Planning Law Firm opening new branch in Florida

I am an experienced estate planning attorney that recently relocated to Florida. Looking for a banner Ad to place on platforms such as HomeLane, Chatterbox and Picturely to create publicity for firm and new leads.

```html
<!DOCTYPE html>
<html lang="en">
<head>
<meta charset="utf-8">
<title>Calmhaven Law Firm – Welcome</title>
<link href="https://fonts.googleapis.com/css2?family=Merriweather:wght@700;900&family=Roboto:wght@400;500&display=swap" rel="stylesheet">
<style>
  :root {
    --navy: #2b405d;
    --navy-deep: #1f3048;
    --navy-light: #3a5373;
    --teal: #1b6b6c;
    --white: #ffffff;
    --dot: #8e9cb0;
    --photo-warm: #a9806a;
    --photo-dark: #2a3447;
  }
  * { margin: 0; padding: 0; box-sizing: border-box; }
  html, body { width: 960px; height: 1200px; overflow: hidden; }
  body { font-family: "Roboto", Arial, sans-serif; color: var(--white); }

  .banner {
    position: relative;
    width: 960px;
    height: 1200px;
    overflow: hidden;
    background:
      linear-gradient(155deg, rgba(255,255,255,0.04) 0 20%, transparent 20% 60%, rgba(255,255,255,0.03) 60% 75%, transparent 75%),
      linear-gradient(180deg, var(--navy-light) 0%, var(--navy) 45%, var(--navy-deep) 100%);
  }

  .brand { position: absolute; left: 59px; top: 40px; display: flex; align-items: center; gap: 10px; }
  .brand-mark { width: 30px; height: 30px; background: var(--white); }
  .brand-text { display: flex; flex-direction: column; align-items: center; }
  .brand-name { font-family: "Merriweather", Georgia, serif; font-weight: 700; font-size: 28px; letter-spacing: 0.5px; line-height: 1; }
  .brand-sub { display: flex; align-items: center; gap: 6px; font-size: 11.5px; letter-spacing: 0.5px; margin-top: 4px; }
  .brand-sub::before, .brand-sub::after { content: ""; width: 40px; height: 1.5px; background: var(--white); }

  .accent-left { position: absolute; left: 43px; top: 144px; width: 49px; }
  .accent-left .teal { height: 78px; background: var(--teal); }
  .accent-left .white { height: 25px; background: var(--white); }

  .photo {
    position: absolute; left: 334px; top: 83px; width: 575px; height: 1006px;
    background:
      linear-gradient(180deg, rgba(169,128,106,0.9) 0%, rgba(140,105,90,0.6) 25%, transparent 45%),
      linear-gradient(90deg, #3b3f4c 0%, var(--photo-dark) 40%, #243049 70%, #2f3b52 100%);
  }

  .accent-right { position: absolute; left: 886px; top: 57px; width: 48px; height: 136px; border: 2px solid var(--white); background: var(--teal); }
  .accent-right::before { content: ""; position: absolute; left: 0; top: 0; right: 0; height: 20px; background: var(--white); }

  .headline {
    position: absolute; left: 60px; top: 280px;
    font-family: "Merriweather", Georgia, serif; font-weight: 900;
    font-size: 58px; line-height: 80px; letter-spacing: -0.5px;
  }
  .headline-rule { position: absolute; left: 60px; top: 461px; width: 116px; height: 3px; background: var(--teal); }

  .intro { position: absolute; left: 60px; top: 494px; width: 330px; font-size: 15.5px; line-height: 26.7px; }
  .intro p + p { margin-top: 8px; }

  .glass { position: absolute; left: 291px; top: 802px; width: 222px; height: 139px; background: rgba(255,255,255,0.2); }
  .bar { position: absolute; left: 183px; top: 860px; display: flex; height: 47px; }
  .bar .white { width: 22px; background: var(--white); }
  .bar .teal { width: 231px; background: var(--teal); }

  .dots { position: absolute; display: grid; }
  .dots span { border-radius: 50%; background: var(--dot); }
  .dots-top { left: 452px; top: 0; grid-template-columns: repeat(6, 3px); gap: 8px; }
  .dots-top span { width: 3px; height: 3px; opacity: 0.6; }
  .dots-bottom { left: 824px; top: 1076px; grid-template-columns: repeat(4, 8px); column-gap: 13px; row-gap: 11px; }
  .dots-bottom span { width: 8px; height: 8px; opacity: 0.8; }

  .contact { position: absolute; left: 58px; display: flex; align-items: center; gap: 8px; font-size: 17px; font-weight: 500; }
  .contact svg { width: 16px; height: 16px; fill: var(--white); }
  .contact-phone { top: 1097px; }
  .contact-email { top: 1143px; }
</style>
</head>
<body>
<div class="banner">
  <div class="dots dots-top"><span></span><span></span><span></span><span></span><span></span><span></span><span></span><span></span><span></span><span></span><span></span><span></span><span></span><span></span><span></span><span></span><span></span><span></span></div>

  <div class="brand">
    <div class="brand-mark"></div>
    <div class="brand-text">
      <div class="brand-name">CALMHAVEN</div>
      <div class="brand-sub">LAW FIRM, PLLC</div>
    </div>
  </div>

  <div class="accent-left"><div class="teal"></div><div class="white"></div></div>

  <div class="photo" role="img" aria-label="Photo of the two attorneys, a smiling woman and man in business attire, seated in front of a brick wall"></div>
  <div class="accent-right"></div>

  <h1 class="headline">Welcome To<br>Calmhaven</h1>
  <div class="headline-rule"></div>

  <div class="intro">
    <p>Where our mission is to bring peace of mind to working families through comprehensive estate planning, wealth management, and tax planning services.</p>
    <p>Calmhaven offers its clients a well-rounded suite of services that not only address immediate financial and legal needs but also sets up a framework for long-term security and Harmony. This approach helps clients feel more in control of their financial destiny.</p>
  </div>

  <div class="glass"></div>
  <div class="bar"><div class="white"></div><div class="teal"></div></div>

  <div class="dots dots-bottom"><span></span><span></span><span></span><span></span><span></span><span></span><span></span><span></span></div>

  <div class="contact contact-phone">
    <svg viewBox="0 0 16 16" aria-hidden="true"><rect x="0" y="0" width="16" height="16" rx="3"/><path d="M5 3.5l1.6 0 .8 2.4-1 .8c.6 1.3 1.6 2.3 2.9 2.9l.8-1 2.4.8 0 1.6c0 .6-.5 1-1 1C7 12 4 9 4 4.5c0-.5.4-1 1-1z" fill="#2b405d"/></svg>
    <span>Phone Call: (555) 014-2290</span>
  </div>
  <div class="contact contact-email">
    <svg viewBox="0 0 18 14" aria-hidden="true" style="width:19px;height:15px"><rect x="0" y="0" width="18" height="14" rx="2"/><path d="M1 1.5l8 6 8-6" stroke="#2b405d" stroke-width="1.6" fill="none"/></svg>
    <span>Send Email: hello@calmhaven.law</span>
  </div>
</div>
</body>
</html>
```